Pop Up Banner Design (30x72in) for events for Orbis Tongue Academy

30 x 72 inch design for a pop up banner or 2 (or 3) to advertise my business, Orbis Tongue Academy, featuring www.orbistongueacademy.com

This banner will be used at anime conventions, or local events to promote the business to the general public, schools, or asian culture lovers.

Color scheme to identify with the logo that is attached. Imagery would be great!

Target audience: teens to 30s
Benefits OTA Offers: learning japanese language, learning japanese culture, peer study groups and events, one-on-one or classroom setting, in person or virtual learning, Kestrel Fluency Grading Exam (KFGE) preparation, homework, guided tours to Japan once a year, translation services, conversation tables, etc.

Target Market(s)

teens to 30 year olds

Industry/Entity Type

Education

Font styles to use
Sans Serif

Colors
ec1f27
ffffff
000000

Requirements
Must have
• logo, imagery, benefits strategically explained, website

```html
<!DOCTYPE html>
<html lang="en">
<head>
<meta charset="utf-8">
<title>Orbis Tongue Academy – Event Banner</title>
<link rel="stylesheet" href="https://fonts.googleapis.com/css2?family=PT+Sans+Narrow&family=Fira+Sans:wght@700&family=Open+Sans:wght@400&display=swap">
<style>
  :root {
    --brand-red: #b8172b;
    --wave-edge: #2b2a30;
    --ink-dark: #18171c;
    --paper: #ffffff;
    --logo-ink: #1e1e22;
  }
  * { margin: 0; padding: 0; box-sizing: border-box; }
  html, body { width: 1200px; height: 2880px; overflow: hidden; background: var(--paper); }
  .banner { position: relative; width: 1200px; height: 2880px; overflow: hidden; background: var(--paper); }

  .scenery-photo { position: absolute; left: 0; top: 300px; width: 1200px; height: 1800px; }
  .wave-backdrop { position: absolute; left: 0; top: 0; width: 1200px; height: 2880px; }

  .brand-mark { position: absolute; left: 0; top: 58px; width: 1200px; text-align: center; }
  .brand-dot { display: block; width: 326px; height: 326px; margin: 0 auto; border-radius: 50%; background: var(--brand-red); }
  .brand-name {
    margin-top: 20px;
    font-family: "PT Sans Narrow", sans-serif; font-weight: 400;
    font-size: 58px; letter-spacing: 1px; color: var(--logo-ink); line-height: 1;
  }

  .benefits { position: absolute; left: 192px; top: 1765px; color: var(--paper); }
  .benefits-title { font-family: "Fira Sans", sans-serif; font-weight: 700; font-size: 37px; line-height: 1; margin-bottom: 20px; }
  .benefits-list { list-style: none; font-family: "Open Sans", sans-serif; font-size: 33px; line-height: 66px; margin-left: -24px; }
  .benefits-list li { position: relative; padding-left: 24px; }
  .benefits-list li::before { content: ""; position: absolute; left: 0; top: 29px; width: 10px; height: 10px; border-radius: 50%; background: var(--paper); }
  .benefits-list .continued { line-height: 40px; margin-top: -14px; padding-left: 12px; }
  .benefits-list .continued::before { display: none; }

  .cta { position: absolute; left: 0; top: 2465px; width: 1200px; text-align: center; color: var(--paper); font-family: "Open Sans", sans-serif; }
  .cta-lead, .cta-tail { font-size: 52px; line-height: 76px; }
  .cta-url { font-size: 60px; line-height: 82px; }
</style>
</head>
<body>
<main class="banner">

  <svg class="scenery-photo" role="img" aria-label="Photo of a red torii gate beside a pond among pine trees and autumn foliage" viewBox="0 0 1200 1800" preserveAspectRatio="none">
    <defs>
      <linearGradient id="scene-tone" x1="0" y1="0" x2="0" y2="1">
        <stop offset="0" stop-color="#ffffff"/>
        <stop offset="0.12" stop-color="#dfe3dc"/>
        <stop offset="0.3" stop-color="#5d6e47"/>
        <stop offset="0.55" stop-color="#3f5232"/>
        <stop offset="0.7" stop-color="#7a5a3c"/>
        <stop offset="0.85" stop-color="#4c5240"/>
        <stop offset="1" stop-color="#2f3a30"/>
      </linearGradient>
    </defs>
    <rect width="1200" height="1800" fill="url(#scene-tone)"/>
  </svg>

  <svg class="wave-backdrop" viewBox="0 0 625 1500" preserveAspectRatio="none" aria-hidden="true">
    <path d="M0,1000 C60,830 200,790 330,760 C480,730 580,670 625,555 L625,1257 L0,1257 Z" fill="var(--wave-edge)"/>
    <path d="M0,1050 C60,875 200,822 330,792 C480,762 585,705 625,610 L625,1257 L0,1257 Z" fill="var(--brand-red)"/>
    <rect x="0" y="1257" width="625" height="6" fill="var(--paper)"/>
    <rect x="0" y="1263" width="625" height="152" fill="var(--ink-dark)"/>
    <rect x="0" y="1415" width="625" height="5" fill="var(--paper)"/>
    <rect x="0" y="1420" width="625" height="80" fill="var(--ink-dark)"/>
  </svg>

  <header class="brand-mark">
    <span class="brand-dot"></span>
    <p class="brand-name">ORBIS TONGUE ACADEMY</p>
  </header>

  <section class="benefits">
    <h2 class="benefits-title">OTA Can Help You:</h2>
    <ul class="benefits-list">
      <li>Learn Japanese</li>
      <li>Virtually or In Person*</li>
      <li>One on One or Classroom setting</li>
      <li>Experience Japanese Culture</li>
      <li>Prep for the KFGE</li>
      <li>Connect with other learners</li>
      <li>One on one homework correction</li>
      <li>Practice speaking with virtual conversation tables</li>
      <li class="continued">and more!</li>
    </ul>
  </section>

  <footer class="cta">
    <p class="cta-lead">Check out</p>
    <p class="cta-url">www.OrbisTongueAcademy.com</p>
    <p class="cta-tail">for more details</p>
  </footer>

</main>
</body>
</html>
```